Business card design

Hi,
I need to have a business card design based on the current logo.
If competitive I not put it out to everyone.

It can be single of double sided

Target Market(s)

Food businesses

Industry/Entity Type

Food Manufacturing

Contact Information for Business Card

Details will on card will be as follows Name = Marcus Bell Email = Marcus@PanHearth.com.au Phone = 0418563207 Address = 57 Larkin Street , Ashgrove Vale QLD 4072 Australia

Font styles to use
Other font styles liked:
• based on two fonts - Adelle & Museo

Requirements
Must have
• Based on the on switch concept

```html
<!DOCTYPE html>
<html lang="en">
<head>
<meta charset="utf-8">
<title>PanHearth Business Card</title>
<link rel="stylesheet" href="https://fonts.googleapis.com/css2?family=Arimo:wght@400;700&family=Arvo:wght@400;700&display=swap">
<style>
  :root {
    --backdrop: #2a2523;
    --card: #0d0d0d;
    --accent: #ea2a4c;
    --text: #ffffff;
    --steel: #b9b9b9;
    --card-w: 540px;
    --card-h: 309px;
  }
  * { box-sizing: border-box; margin: 0; padding: 0; }
  html, body {
    width: 1200px;
    height: 842px;
    overflow: hidden;
    background: var(--backdrop);
  }
  .canvas {
    position: relative;
    width: 1200px;
    height: 842px;
    display: flex;
    align-items: center;
    justify-content: center;
    gap: 40px;
  }
  .card {
    position: relative;
    width: var(--card-w);
    height: var(--card-h);
    background: var(--card);
    overflow: hidden;
    box-shadow: 0 10px 30px rgba(0, 0, 0, 0.45);
  }

  /* Contact side */
  .card--contact .band {
    position: absolute;
    left: 0;
    right: 0;
    height: 13px;
    background: var(--accent);
  }
  .card--contact .band--top { top: 10px; }
  .card--contact .band--bottom { bottom: 10px; }
  .contact {
    position: absolute;
    inset: 0;
    display: flex;
    flex-direction: column;
    align-items: center;
    justify-content: center;
    text-align: center;
    font-family: "Arimo", Arial, sans-serif;
    color: var(--text);
  }
  .contact__name {
    font-weight: 700;
    font-size: 20px;
    letter-spacing: 1.5px;
    color: var(--accent);
    text-transform: uppercase;
  }
  .contact__rule {
    width: 92px;
    height: 1px;
    background: var(--accent);
    margin: 7px 0 9px;
  }
  .contact__lines {
    font-size: 14px;
    line-height: 1.3;
  }

  /* Brand side */
  .card--brand .tab {
    position: absolute;
    width: 26px;
    height: 62px;
    background: var(--accent);
  }
  .card--brand .tab::after {
    content: "";
    position: absolute;
    top: 0;
    width: 4px;
    height: 100%;
    background: var(--steel);
  }
  .card--brand .tab--left { left: 0; top: 178px; }
  .card--brand .tab--left::after { right: -8px; }
  .card--brand .tab--right { right: 0; top: 62px; }
  .card--brand .tab--right::after { left: -8px; }
  .brand {
    position: absolute;
    inset: 0;
    display: flex;
    align-items: center;
    justify-content: center;
    gap: 14px;
  }
  .brand__dot {
    width: 34px;
    height: 34px;
    border-radius: 50%;
    background: var(--accent);
    flex: none;
  }
  .brand__text { display: flex; flex-direction: column; }
  .brand__name {
    font-family: "Arimo", Arial, sans-serif;
    font-weight: 700;
    font-size: 44px;
    letter-spacing: 1px;
    color: var(--text);
    text-transform: uppercase;
    line-height: 1;
  }
  .brand__tagline {
    font-family: "Arvo", Georgia, serif;
    font-size: 12px;
    color: var(--text);
    text-align: right;
    margin-top: 4px;
  }
</style>
</head>
<body>
  <main class="canvas">
    <section class="card card--contact" aria-label="Contact side">
      <div class="band band--top"></div>
      <div class="band band--bottom"></div>
      <div class="contact">
        <p class="contact__name">Marcus Bell</p>
        <div class="contact__rule"></div>
        <p class="contact__lines">57 Larkin Street<br>Ashgrove Vale<br>QLD 4072 Australia</p>
        <div class="contact__rule"></div>
        <p class="contact__lines">0418563207<br>Marcus@PanHearth.com.au<br>www.PanHearth.com.au</p>
      </div>
    </section>

    <section class="card card--brand" aria-label="Brand side">
      <div class="tab tab--left"></div>
      <div class="tab tab--right"></div>
      <div class="brand">
        <span class="brand__dot"></span>
        <div class="brand__text">
          <p class="brand__name">PanHearth</p>
          <p class="brand__tagline">Fresh Kitchens Made Simple</p>
        </div>
      </div>
    </section>
  </main>
</body>
</html>
```